A-Stand Directional Sign Design

Objective:
We need a professional graphic design for an A-Stand sign that will guide customers arriving in our parking lot to our office. The design should be visually clear, welcoming, and aligned with our brand identity.
REQUIREMENTS:
Two versions of the design:
- One with an arrow pointing left
- One with an arrow pointing right
(This allows us to place the A-Stand anywhere and flip the graphic as needed.)
DIMENSIONS:
- Viewable Area: 30" x 40"
BRAND ALIGNMENT:
- Colors, fonts, and overall style should match our website: www.glidemarrow.com
- Clean, modern, and professional look consistent with our aviation/tourism brand
CONTENT:
- Clear directional arrow (left or right depending on version)
- Text: “Office Entrance” or similar concise wording (designers may propose alternatives if they improve clarity)
READABILITY:
- Bold, high-contrast design for visibility from a distance
- Simple layout that avoids clutter
DELIVERABLES:
- Final artwork in print-ready format (PDF preferred)
- Two versions: Arrow Left and Arrow Right
DESIGN GOAL:
Ensure customers can easily find our office upon arrival, while reinforcing glideMARROW’s professional and welcoming brand image.
Target Market(s)
Tourism
Look and feel

```html
<!DOCTYPE html>
<html lang="en">
<head>
<meta charset="utf-8">
<title>glideMARROW – Office Entrance A-Stand Sign</title>
<link href="https://fonts.googleapis.com/css2?family=Poppins:wght@500;600&display=swap" rel="stylesheet">
<style>
  :root {
    --page-bg: #f9f9fc;
    --brand-blue: #1a68b5;
    --brand-blue-deep: #0e4a8f;
    --brand-blue-mid: #2a7cc4;
    --sky-light: #eef3f8;
    --sign-white: #ffffff;
    --logo-grey: #e9ecef;
    --cabin-light: #d9d6d3;
    --cabin-warm: #d8b9a4;
    --cabin-dark: #4a5356;
  }
  * { margin: 0; padding: 0; box-sizing: border-box; }
  html, body {
    width: 1200px;
    height: 1200px;
    overflow: hidden;
    background: var(--page-bg);
    font-family: "Poppins", Arial, sans-serif;
  }
  .sign {
    position: absolute;
    left: 75px;
    top: 168px;
    width: 1050px;
    height: 787px;
    overflow: hidden;
  }
  .aerial-backdrop {
    position: absolute;
    inset: 0;
    background:
      radial-gradient(ellipse 520px 300px at 560px 30px, var(--sky-light) 0%, rgba(238,243,248,0.85) 35%, rgba(238,243,248,0) 100%),
      linear-gradient(180deg, var(--brand-blue-mid) 0%, var(--brand-blue) 45%, var(--brand-blue-deep) 100%);
  }
  .brand-name {
    position: absolute;
    left: 105px;
    top: 128px;
    font-weight: 500;
    font-size: 34px;
    letter-spacing: 0.5px;
    color: var(--logo-grey);
  }
  .headline {
    position: absolute;
    left: 105px;
    top: 270px;
    font-weight: 500;
    font-size: 212px;
    line-height: 1;
    letter-spacing: -2px;
    color: var(--sign-white);
  }
  .subline {
    position: absolute;
    left: 106px;
    top: 480px;
    font-weight: 500;
    font-size: 57px;
    line-height: 1;
    color: var(--logo-grey);
  }
  .direction-arrow {
    position: absolute;
    left: 104px;
    top: 634px;
  }
  .passenger-photo {
    position: absolute;
    inset: 0;
  }
</style>
</head>
<body>
  <main class="sign">
    <div class="aerial-backdrop" role="img" aria-label="Blue-tinted aerial view of a city seen from a helicopter"></div>

    <div class="brand-name">glideMARROW</div>

    <h1 class="headline">Office</h1>
    <p class="subline">Entrance</p>

    <svg class="direction-arrow" width="280" height="100" viewBox="0 0 280 100" aria-label="Arrow pointing right">
      <polygon points="0,27 187,27 187,0 270,48 187,95 187,71 0,71" fill="var(--sign-white)"/>
    </svg>

    <svg class="passenger-photo" width="1050" height="787" viewBox="0 0 1050 787" role="img" aria-label="Photo of a smiling passenger wearing an aviation headset, looking out of a helicopter window">
      <defs>
        <linearGradient id="cabinTone" x1="0" y1="0" x2="1" y2="1">
          <stop offset="0" stop-color="var(--cabin-light)"/>
          <stop offset="0.45" stop-color="var(--cabin-warm)"/>
          <stop offset="0.75" stop-color="#c9d3d6"/>
          <stop offset="1" stop-color="var(--cabin-dark)"/>
        </linearGradient>
      </defs>
      <path d="M801,0 C740,200 690,420 650,787 L1050,787 L1050,0 Z" fill="url(#cabinTone)"/>
    </svg>
  </main>
</body>
</html>
```